Corvane Freight Company Business Card Design

We are a company that delivers natural saltwater (from the ocean) to aquarium companies, restaurants and home marine tanks. I would like a new business card to suit.

Must include Name, company name, abn, contact number and website as well as logo (see attached).

Looking for a design that stands out, has a clean but unique appearance.

Double and single sided entries welcome

Business

• Logo

```html
<!DOCTYPE html>
<html lang="en">
<head>
<meta charset="utf-8">
<title>Corvane Freight Company – Business Card</title>
<link rel="stylesheet" href="https://fonts.googleapis.com/css2?family=Mulish:wght@400;800&display=swap">
<style>
  :root {
    --backdrop: #2b2b2b;
    --front-blue: #2f7fe6;
    --front-top: #3a8bef;
    --front-rule: #9fd0ff;
    --back-blue: #3fb0f0;
    --ink-light: #ffffff;
    --ink-soft: #e6f2ff;
    --divider: #9fc8f5;
  }
  * { box-sizing: border-box; margin: 0; padding: 0; }
  html, body {
    width: 1200px;
    height: 1026px;
    overflow: hidden;
    background: var(--backdrop);
    font-family: "Mulish", "Century Gothic", sans-serif;
    color: var(--ink-light);
  }
  .stage { position: relative; width: 1200px; height: 1026px; }

  .card {
    position: absolute;
    width: 732px;
    height: 416px;
    border-radius: 36px;
    overflow: hidden;
  }

  /* Front side */
  .card--front { left: 91px; top: 56px; background: var(--front-blue); }
  .card--front .top-band {
    position: absolute; left: 0; top: 0; width: 100%; height: 109px;
    background: var(--front-top);
    border-bottom: 3px solid var(--front-rule);
  }
  .brand-name {
    position: absolute; left: 0; width: 100%;
    text-align: center;
    font-weight: 800;
    font-size: 46px;
    letter-spacing: -0.5px;
    color: var(--ink-light);
  }
  .card--front .brand-name { top: 114px; }
  .holder {
    position: absolute; top: 240px; width: 100%;
    text-align: center; font-size: 24px;
  }
  .holder .holder-name { font-weight: 800; }
  .holder .holder-title { font-weight: 400; font-size: 20px; color: var(--ink-soft); }

  .contact { position: absolute; top: 306px; left: 0; width: 100%; height: 80px; }
  .contact .address {
    position: absolute; right: 368px; top: 4px;
    text-align: right; font-size: 18px; line-height: 25px;
    color: var(--ink-soft);
  }
  .contact .rule {
    position: absolute; left: 384px; top: 0; width: 1px; height: 80px;
    background: var(--divider);
  }
  .contact .lines {
    position: absolute; left: 400px; top: 0;
    list-style: none; font-size: 18px; line-height: 27px;
    color: var(--ink-soft);
  }
  .contact .lines li { display: flex; align-items: center; gap: 6px; }
  .contact .lines svg { width: 14px; height: 14px; fill: var(--ink-soft); }

  /* Back side */
  .card--back { left: 365px; top: 527px; background: var(--back-blue); }
  .card--back .brand-name { top: 160px; font-size: 50px; }
  .card--back .web {
    position: absolute; top: 340px; width: 100%;
    text-align: center; font-size: 22px; letter-spacing: 5px;
    color: var(--ink-light);
  }
</style>
</head>
<body>
<main class="stage">
  <section class="card card--front" aria-label="Business card, front">
    <div class="top-band"></div>
    <h1 class="brand-name">Corvane Freight Company</h1>
    <p class="holder"><span class="holder-name">Your name,</span> <span class="holder-title">Title</span></p>
    <div class="contact">
      <p class="address">Corvane Freight LLC<br>Street Name, City Name<br>State, City Zip Code</p>
      <div class="rule"></div>
      <ul class="lines">
        <li><svg viewBox="0 0 16 16" aria-hidden="true"><path d="M3.5 1.5l2.5 0 1 3.5-1.7 1.2a8 8 0 0 0 4.5 4.5L11 9l3.5 1v2.5c0 1-1 2-2 2A11 11 0 0 1 1.5 3.5c0-1 1-2 2-2z"/></svg>123-456-7890</li>
        <li><svg viewBox="0 0 16 16" aria-hidden="true"><circle cx="8" cy="8" r="6.5"/></svg>www.website.com</li>
        <li>ABN : 0123456789</li>
      </ul>
    </div>
  </section>

  <section class="card card--back" aria-label="Business card, back">
    <h2 class="brand-name">Corvane Freight Company</h2>
    <p class="web">www.website.com</p>
  </section>
</main>
</body>
</html>
```